Brookvale Building Company - advertisement poster

I am looking to print some canvas signs to advertise my general contracting company, Brookvale Building Company. The sign will measure 6' long x 3' high so the size should match that ratio. I already have a logo icon, which is the Letter 'B' and some trees that I would like to incorporate, see attached. I would also like the to have the following information listed:
1) phone number: 831-555-0172
2) email: brookvalebuildingcompany@mailnest.example
3) website: brookvalebuildingcompany.example
4) Lic#4826130
5) I want to use this text: "BUILD WITH THE B-CREW!"

The ad should be relatively simple and clean. Black and Green are my company colors. I am open to creative ideas!

Target Market(s)

People looking to renovate their homes

Industry/Entity Type

Construction

Colors
59FF00
82FF00
B8FF75
E3FFCB
F4FFEA

Requirements
Must have
• Must have my company logo
Should not have
• No photos or complex graphics

```html
<!DOCTYPE html>
<html lang="en">
<head>
<meta charset="utf-8">
<title>Brookvale Building Company – Sign</title>
<link href="https://fonts.googleapis.com/css2?family=Arimo:wght@400;700&display=swap" rel="stylesheet">
<style>
  :root {
    --page-bg: #d9dcdf;
    --sign-bg: #1e1e1e;
    --brand-green: #62b845;
    --text-white: #ffffff;
    --text-soft: #f1f1f1;
    --text-muted: #bdbdbd;
  }
  * { margin: 0; padding: 0; box-sizing: border-box; }
  html, body {
    width: 1200px;
    height: 800px;
    overflow: hidden;
    background: var(--page-bg);
    font-family: "Arimo", Arial, sans-serif;
  }
  .sign {
    position: absolute;
    left: 40px;
    top: 120px;
    width: 1120px;
    height: 560px;
    background: var(--sign-bg);
    color: var(--text-white);
  }
  .brand {
    position: absolute;
    top: 92px;
    left: 0;
    width: 100%;
    display: flex;
    flex-direction: column;
    align-items: center;
    gap: 12px;
  }
  .brand-line {
    display: flex;
    align-items: center;
    gap: 14px;
  }
  .brand-mark {
    width: 22px;
    height: 22px;
    background: var(--brand-green);
  }
  .brand-name {
    font-weight: 700;
    font-size: 28px;
    letter-spacing: 2px;
    text-transform: uppercase;
    color: var(--text-white);
  }
  .license {
    font-size: 15px;
    letter-spacing: 3px;
    color: var(--text-muted);
  }
  .tagline {
    position: absolute;
    top: 268px;
    left: 0;
    width: 100%;
    text-align: center;
    font-weight: 700;
    font-size: 80px;
    line-height: 1;
    letter-spacing: 2px;
    color: var(--brand-green);
  }
  .contact {
    position: absolute;
    top: 440px;
    left: 135px;
    right: 80px;
    display: flex;
    align-items: center;
    justify-content: space-between;
  }
  .phone {
    display: flex;
    align-items: center;
    gap: 18px;
    font-weight: 700;
    font-size: 46px;
    letter-spacing: 1px;
  }
  .online {
    display: flex;
    flex-direction: column;
    gap: 14px;
    font-size: 21px;
    letter-spacing: 0.5px;
    color: var(--text-soft);
  }
  .online-item {
    display: flex;
    align-items: center;
    gap: 18px;
  }
  .icon { flex: none; }
</style>
</head>
<body>
  <main class="sign">
    <div class="brand">
      <div class="brand-line">
        <span class="brand-mark"></span>
        <span class="brand-name">Brookvale Building Company</span>
      </div>
      <span class="license">Lic#4826130</span>
    </div>

    <h1 class="tagline">Build with the B-Crew!</h1>

    <div class="contact">
      <div class="phone">
        <svg class="icon" width="24" height="24" viewBox="0 0 24 24" aria-hidden="true">
          <path d="M6.6 10.8a15 15 0 0 0 6.6 6.6l2.2-2.2a1 1 0 0 1 1-.25 11.4 11.4 0 0 0 3.6.57 1 1 0 0 1 1 1V20a1 1 0 0 1-1 1A17 17 0 0 1 3 4a1 1 0 0 1 1-1h3.5a1 1 0 0 1 1 1c0 1.25.2 2.45.57 3.57a1 1 0 0 1-.25 1z" fill="var(--brand-green)"/>
        </svg>
        <span>831-555-0172</span>
      </div>
      <div class="online">
        <div class="online-item">
          <svg class="icon" width="20" height="20" viewBox="0 0 20 20" aria-hidden="true">
            <g fill="none" stroke="var(--brand-green)" stroke-width="1.6">
              <circle cx="10" cy="10" r="8.5"/>
              <ellipse cx="10" cy="10" rx="3.8" ry="8.5"/>
              <line x1="1.5" y1="10" x2="18.5" y2="10"/>
              <line x1="3" y1="5.5" x2="17" y2="5.5"/>
              <line x1="3" y1="14.5" x2="17" y2="14.5"/>
            </g>
          </svg>
          <span>BrookvaleBuildingCompany.example</span>
        </div>
        <div class="online-item">
          <svg class="icon" width="20" height="16" viewBox="0 0 20 16" aria-hidden="true">
            <rect x="0" y="1" width="20" height="14" fill="var(--brand-green)"/>
            <path d="M0 1.5 10 9 20 1.5" fill="none" stroke="var(--sign-bg)" stroke-width="1.6"/>
          </svg>
          <span>brookvalebuildingcompany@mailnest.example</span>
        </div>
      </div>
    </div>
  </main>
</body>
</html>
```